Website re-design and completion for www.brovimark.com

Graphically redesign and complete the existing site www.brovimark.com
This site intent is to:
a) introduce and educate about a new Technoloy to customers in a variety of different industries using traditional methods.
b) outline and promote the benefits and ROI of using the new techology
c) Sell our machines by showing customers the benefits and reasons to purchase from us over other suppliers
We do want to keep the overall concept. Like the home page with a slider. The most important thing to us is to increase the design of the slider. Next we need it standard layout with some attractive design to describe each product group. There are 3 product groups. Laser Cleaning Machines, Laser Welding Machines and Laser Cutting Machines

Target Market(s)

Mostly business to business.

Coding

Coded - Design and coding required

Font styles to use
Sans Serif
Other font styles liked:
• Calibri, Arial

Requirements
Must have
• A serious approach as we are targeting professionals, such as production managers, engineers and so forth
Should not have
• Annoying call to action stuff. Overly playful gimmicks.

```html
<!DOCTYPE html>
<html lang="en">
<head>
<meta charset="utf-8">
<title>Brovimark Laser – Laser Cutting and Welding Equipment</title>
<link href="https://fonts.googleapis.com/css2?family=Arimo:wght@400;700&family=Figtree:wght@400;600;700&display=swap" rel="stylesheet">
<style>
:root{
  --red:#d11f2d;
  --blue:#1d86cf;
  --ink:#1d1d1f;
  --text:#444;
  --muted:#777;
  --pale:#eef5fa;
  --card:#fbeff0;
  --dark:#232325;
  --line:#dcdcdc;
}
*{box-sizing:border-box;margin:0;padding:0}
html,body{width:1200px;height:4474px;overflow:hidden}
body{position:relative;background:#fff;font-family:"Arimo",Arial,sans-serif;color:var(--text)}
.abs{position:absolute}
.accent{color:var(--blue)}
.btn{position:absolute;background:var(--red);color:#fff;font-weight:700;font-size:13px;display:flex;align-items:center;justify-content:center;border-radius:2px}
.h2{font-family:"Arimo",Arial,sans-serif;font-weight:700;font-size:28px;color:var(--ink)}
.p{font-size:11.5px;line-height:20px;color:var(--text)}
.underline{position:absolute;height:3px;width:52px;background:var(--red)}
.ph{position:absolute}

/* hero */
.hero{position:absolute;left:0;top:0;width:1200px;height:465px;background:linear-gradient(100deg,#17181d 0%,#2a2b33 35%,#1c1f2c 60%,#2c3140 100%);overflow:hidden}
.hero-glow{position:absolute;left:0;top:180px;width:520px;height:285px;background:radial-gradient(ellipse at 20% 60%,rgba(214,120,40,.45),rgba(0,0,0,0) 70%)}
.brand{position:absolute;left:141px;top:28px;color:#fff;font-family:"Figtree",sans-serif;font-weight:700;font-size:36px;letter-spacing:2px;display:flex;align-items:center;gap:10px}
.brand .mark{width:14px;height:14px;background:var(--red)}
.brand-sub{position:absolute;left:165px;top:66px;font-size:9px;color:#d9d9d9;letter-spacing:.5px}
.socials{position:absolute;left:898px;top:46px;display:flex;gap:14px}
.socials span{width:10px;height:10px;border-radius:50%;background:#fff}
.menu{position:absolute;left:1024px;top:34px;width:34px;height:34px;border-radius:50%;background:var(--red)}
.menu i{position:absolute;left:10px;width:14px;height:2px;background:#fff}
.hero h1{position:absolute;left:141px;top:152px;font-family:"Figtree",sans-serif;font-weight:700;font-size:34px;color:#fff}
.hero .lead{position:absolute;left:141px;top:201px;width:300px;font-family:"Figtree",sans-serif;font-size:12px;line-height:22px;color:#ddd}
.ticks{position:absolute;left:141px;top:274px;display:flex;gap:22px;color:#fff;font-family:"Figtree",sans-serif;font-size:12.5px}
.ticks span{display:flex;align-items:center;gap:8px}
.machine{left:598px;top:128px;width:370px;height:310px;border-radius:18px;background:linear-gradient(160deg,#3a3c42,#121316 70%)}
.callout{position:absolute;font-family:"Figtree",sans-serif;font-size:12px;line-height:18px;color:#fff;text-align:center}

/* about */
.about-photo1{left:141px;top:556px;width:366px;height:477px;background:linear-gradient(160deg,#3b2a1c,#8a5a2c 55%,#d9953f)}
.about-circle{left:640px;top:920px;width:90px;height:90px;border-radius:50%;background:#dcebf6}
.about-photo2{left:405px;top:948px;width:285px;height:167px;background:linear-gradient(140deg,#0f2746,#2b5f8f 60%,#9bbbd2)}
.about-machine{left:684px;top:1008px;width:110px;height:112px;border-radius:10px;background:linear-gradient(160deg,#3a3b3f,#0e0f11)}

/* products */
.products{position:absolute;left:0;top:1207px;width:1200px;height:620px;background:var(--pale)}
.tab{position:absolute;top:1327px;height:38px;border:1.5px solid #3a3a3a;font-size:12px;font-weight:700;color:var(--ink);display:flex;align-items:center;justify-content:center;background:#fff}
.tab.active{background:var(--red);color:#fff;border-color:var(--red)}
.prod-photo{left:762px;top:1421px;width:297px;height:332px;background:linear-gradient(150deg,#4a2c18,#b8652a 55%,#f0a24e)}

/* why */
.why-photo1{left:141px;top:1942px;width:257px;height:313px;background:linear-gradient(150deg,#1d3d8a,#6a7fa8 60%,#d5dce6)}
.why-photo2{left:304px;top:1913px;width:217px;height:254px;background:linear-gradient(160deg,#2b2424,#a83822 55%,#f2a44a)}
.dots{position:absolute;left:100px;top:2205px;width:40px;height:80px;background-image:radial-gradient(#8fbde0 1.3px,transparent 1.5px);background-size:12px 12px}
.why-list{position:absolute;left:592px;top:1992px;width:470px;list-style:none}
.why-list li{display:flex;gap:10px;font-size:12.5px;line-height:20px;color:#333;margin-bottom:14px}
.why-list svg{flex:none;margin-top:3px}

/* testimonials */
.t-card{position:absolute;top:2468px;width:448px;height:193px;border-radius:26px;background:var(--card)}
.t-card p{position:absolute;left:35px;top:52px;width:370px;font-size:12px;line-height:22.5px;color:#444}
.t-tail{position:absolute;bottom:-16px;left:90px;width:0;height:0;border-left:14px solid transparent;border-right:14px solid transparent;border-top:16px solid var(--card)}
.quote{position:absolute;top:2443px;width:48px;height:48px;border-radius:50%;background:var(--red);display:flex;align-items:center;justify-content:center}
.avatar{position:absolute;top:2703px;width:76px;height:76px;border-radius:50%;background:linear-gradient(140deg,#c9b9ad,#6f5e55)}
.stars{position:absolute;top:2718px;color:#f2a21b;font-size:15px;letter-spacing:2px}
.t-name{position:absolute;top:2742px;font-weight:700;font-size:16px;color:var(--ink)}

/* network */
.network{position:absolute;left:0;top:2915px;width:1200px;height:524px;background:var(--pale)}
.map{left:135px;top:3035px;width:930px;height:370px;border-radius:8px;background:radial-gradient(ellipse at 50% 50%,#c9ccd1,#dfe5ea 70%,var(--pale))}
.map-tag{position:absolute;left:272px;top:3074px;background:#fff;padding:8px 20px;font-size:13px;color:#333;box-shadow:0 2px 8px rgba(0,0,0,.08)}

/* contact */
.contact-photo{left:141px;top:3524px;width:394px;height:466px;background:linear-gradient(160deg,#3a2a20,#9a5a28 50%,#f3b866)}
.field{position:absolute;height:42px;background:#f3f3f3;font-size:12px;color:#888;padding:0 14px;display:flex;align-items:center;justify-content:space-between}
.field.tall{align-items:flex-start;padding-top:14px}

/* footer */
.footer{position:absolute;left:0;top:4073px;width:1200px;height:401px;background:var(--dark)}
.f-brand{position:absolute;left:141px;top:4216px;color:var(--red);font-family:"Figtree",sans-serif;font-weight:700;font-size:40px;letter-spacing:2px;display:flex;align-items:center;gap:10px}
.f-brand .mark{width:14px;height:14px;background:var(--red)}
.f-call{position:absolute;left:168px;top:4263px;color:#fff;font-size:11px;font-weight:700}
.f-col{position:absolute;top:4130px;color:#fff}
.f-col h4{font-size:17px;font-weight:700;margin-bottom:28px}
.f-col a{display:block;font-size:12px;color:#ddd;text-decoration:none;height:30px}
.f-contact{display:flex;align-items:center;gap:10px;font-size:12px;color:#ddd;height:35px}
.f-rule{position:absolute;left:141px;top:4412px;width:918px;height:1px;background:#444}
.copy{position:absolute;left:141px;top:4436px;font-size:10.5px;color:#ccc}
.f-social{position:absolute;top:4428px;width:26px;height:26px;border-radius:50%;background:#fff;border:3px solid var(--red)}
</style>
</head>
<body>

<!-- Hero -->
<header class="hero">
  <div class="hero-glow"></div>
  <div class="brand"><span class="mark"></span>BROVIMARK</div>
  <div class="brand-sub">LASER CUTTING AND WELDING EQUIPMENT</div>
  <div class="socials"><span></span><span></span><span></span><span></span><span></span></div>
  <div class="menu"><i style="top:12px"></i><i style="top:16px"></i><i style="top:20px"></i></div>

  <h1>Laser Welding</h1>
  <p class="lead">With Unmatched Precision, Laser Welding Is Easy To Learn, Energy Efficient, And Remarkably Fast Compared To MIG And TIG Welding.</p>
  <div class="ticks">
    <span><svg width="16" height="16" viewBox="0 0 16 16"><circle cx="8" cy="8" r="7" fill="none" stroke="#d11f2d" stroke-width="1.5"/><path d="M4.5 8.2l2.4 2.4 4.6-4.8" fill="none" stroke="#d11f2d" stroke-width="1.6"/></svg>Compact</span>
    <span><svg width="16" height="16" viewBox="0 0 16 16"><circle cx="8" cy="8" r="7" fill="none" stroke="#d11f2d" stroke-width="1.5"/><path d="M4.5 8.2l2.4 2.4 4.6-4.8" fill="none" stroke="#d11f2d" stroke-width="1.6"/></svg>Light</span>
    <span><svg width="16" height="16" viewBox="0 0 16 16"><circle cx="8" cy="8" r="7" fill="none" stroke="#d11f2d" stroke-width="1.5"/><path d="M4.5 8.2l2.4 2.4 4.6-4.8" fill="none" stroke="#d11f2d" stroke-width="1.6"/></svg>Portable</span>
  </div>
  <div class="btn" style="left:141px;top:313px;width:115px;height:36px">Contact Us</div>

  <div class="ph machine" role="img" aria-label="Handheld laser welding machine with control panel and torch"></div>

  <svg class="abs" style="left:0;top:0" width="1200" height="465">
    <g fill="none" stroke="#3f8fd6" stroke-width="1.3">
      <polyline points="666,160 710,160 790,275"/>
      <polyline points="1020,170 960,185 900,195"/>
      <polyline points="588,288 640,288 690,285"/>
      <polyline points="1000,245 935,250 895,255"/>
      <polyline points="998,266 960,270 930,270"/>
      <polyline points="1016,300 940,300 895,302"/>
      <polyline points="1005,356 920,330 890,320"/>
      <path d="M450 465 Q600 440 750 465" stroke-width="1.5"/>
    </g>
    <g fill="#3f8fd6"><circle cx="790" cy="275" r="3"/><circle cx="900" cy="195" r="3"/><circle cx="690" cy="285" r="3"/><circle cx="895" cy="255" r="3"/><circle cx="930" cy="270" r="3"/><circle cx="895" cy="302" r="3"/><circle cx="890" cy="320" r="3"/></g>
  </svg>
  <div class="callout" style="left:570px;top:139px;width:94px">Laser<br>Control Switch</div>
  <div class="callout" style="left:1010px;top:151px;width:160px">Gas Pressure Detection,<br>Control Switch And<br>Security Alarm</div>
  <div class="callout" style="left:455px;top:260px;width:140px">Welding Torch<br>Trigger Switch, Torch<br>Button</div>
  <div class="callout" style="left:1000px;top:236px;width:90px;text-align:left">Warning Lamp</div>
  <div class="callout" style="left:998px;top:257px;width:120px;text-align:left">Safety Key Switch</div>
  <div class="callout" style="left:1012px;top:297px;width:140px">Emergency Stop Button,<br>Laser Power Switch</div>
  <div class="callout" style="left:1005px;top:347px;width:130px">LOOP Safety Interlock</div>
</header>

<!-- About -->
<section>
  <div class="ph about-photo1" role="img" aria-label="Industrial laser heads cutting metal with sparks"></div>
  <div class="ph about-circle"></div>
  <div class="ph about-photo2" role="img" aria-label="Laser cutter working on a metal sheet"></div>
  <div class="ph about-machine" role="img" aria-label="Compact laser machine unit"></div>
  <h2 class="h2 abs" style="left:582px;top:556px">About <span class="accent">Us</span></h2>
  <p class="p abs" style="left:582px;top:624px;width:475px">At Brovimark Laser, we're dedicated to providing you with top-of-the-line equipment that you can rely on for all your manufacturing requirements. With years of expertise in the manufacturing industry, we understand the importance of laser photonics equipment and the myriad questions that may arise when integrating laser technology into your operations. That's why we're here to offer comprehensive support and guidance every step of the way.</p>
  <p class="p abs" style="left:582px;top:739px;width:475px">Our team at Brovimark Laser boasts extensive experience working directly within manufacturing processes, giving us unique insights into the challenges and demands of the industry. We meticulously test all our products to ensure they not only meet but exceed your expectations.</p>
  <div class="btn" style="left:582px;top:847px;width:108px;height:36px">Learn More</div>
</section>

<!-- Products -->
<section class="products"></section>
<h2 class="h2 abs" style="left:0;width:1200px;text-align:center;top:1256px">Our <span class="accent">Products</span></h2>
<div class="tab" style="left:398px;width:130px">Laser Cleaning</div>
<div class="tab active" style="left:542px;width:125px">Laser Welding</div>
<div class="tab" style="left:681px;width:121px">Laser Cutting</div>
<h3 class="abs" style="left:141px;top:1442px;font-size:22px;font-weight:700;color:var(--ink)">Laser Welding Machines</h3>
<p class="p abs" style="left:141px;top:1496px;width:500px">With unmatched precision, laser welding is easy to learn, energy efficient, and remarkably fast compared to MIG and TIG welding. Handheld laser welding machines offer unparalleled speed, precision, and ease compared to traditional methods like MIG and TIG welding.</p>
<p class="p abs" style="left:141px;top:1570px;width:500px">With its cutting-edge features, the MX1 is remarkably easy to learn and operate. Equipped with a user-friendly 7" LED touch screen and an intelligent operating system supporting multiple languages, this system simplifies the welding process like never before. The ARGO MX1-Series features an intuitive, easy-to-use interface, based on feedback from welders like you.</p>
<div class="btn" style="left:141px;top:1678px;width:109px;height:36px">Learn More</div>
<div class="ph prod-photo" role="img" aria-label="Handheld laser welding torch producing sparks"></div>

<!-- Why choose -->
<section>
  <div class="dots"></div>
  <div class="ph why-photo1" role="img" aria-label="Laser cutting head over a worktable"></div>
  <div class="ph why-photo2" role="img" aria-label="Laser nozzle cutting metal with glowing sparks"></div>
  <h2 class="h2 abs" style="left:592px;top:1926px">Why Choose Our <span class="accent">Technology?</span></h2>
  <div class="underline" style="left:592px;top:1966px"></div>
  <ul class="why-list">
    <li><svg width="18" height="16" viewBox="0 0 18 16"><path d="M2 2l14 6-14 6 3-6z" fill="none" stroke="#1d86cf" stroke-width="1.4"/><path d="M5 8h8" stroke="#d11f2d" stroke-width="1.4"/></svg>we are committed to providing you with the highest quality equipment that you can depend on for your manufacturing needs.</li>
    <li><svg width="18" height="16" viewBox="0 0 18 16"><path d="M2 2l14 6-14 6 3-6z" fill="none" stroke="#1d86cf" stroke-width="1.4"/><path d="M5 8h8" stroke="#d11f2d" stroke-width="1.4"/></svg>We understand the manufacturing industry, the uses of laser photonics equipment.</li>
    <li><svg width="18" height="16" viewBox="0 0 18 16"><path d="M2 2l14 6-14 6 3-6z" fill="none" stroke="#1d86cf" stroke-width="1.4"/><path d="M5 8h8" stroke="#d11f2d" stroke-width="1.4"/></svg>Brovimark Laser has extensive experience working directly with the manufacturing process.</li>
    <li><svg width="18" height="16" viewBox="0 0 18 16"><path d="M2 2l14 6-14 6 3-6z" fill="none" stroke="#1d86cf" stroke-width="1.4"/><path d="M5 8h8" stroke="#d11f2d" stroke-width="1.4"/></svg>Laser technology has made a revolutionary impact on manufacturing.</li>
    <li><svg width="18" height="16" viewBox="0 0 18 16"><path d="M2 2l14 6-14 6 3-6z" fill="none" stroke="#1d86cf" stroke-width="1.4"/><path d="M5 8h8" stroke="#d11f2d" stroke-width="1.4"/></svg>Laser manufacturing is quickly becoming the new standard due to its efficiency, convenience, and precision.</li>
  </ul>
</section>

<!-- Testimonials -->
<section>
  <h2 class="h2 abs" style="left:0;width:1200px;text-align:center;top:2364px">What Our Happy <span class="accent">Clients Say</span></h2>
  <div class="t-card" style="left:141px"><p>This is due to their excellent service, competitive pricing and customer support. It's thoroughly refreshing to get such a personal touch. There are many variations of passages of Lorem Ipsum available, but the majority have suffered alteration in some form.</p><div class="t-tail"></div></div>
  <div class="t-card" style="left:611px"><p>This is due to their excellent service, competitive pricing and customer support. It's thoroughly refreshing to get such a personal touch. There are many variations of passages of Lorem Ipsum available, but the majority have suffered alteration in some form.</p><div class="t-tail"></div></div>
  <div class="quote" style="left:198px"><svg width="22" height="18" viewBox="0 0 22 18"><path d="M2 2h7v7l-3 7H3l2-7H2zM13 2h7v7l-3 7h-3l2-7h-3z" fill="#fff"/></svg></div>
  <div class="quote" style="left:667px"><svg width="22" height="18" viewBox="0 0 22 18"><path d="M2 2h7v7l-3 7H3l2-7H2zM13 2h7v7l-3 7h-3l2-7h-3z" fill="#fff"/></svg></div>
  <div class="avatar" style="left:205px" role="img" aria-label="Client portrait"></div>
  <div class="stars" style="left:295px">★★★★★</div>
  <div class="t-name" style="left:295px">Laura Mendel</div>
  <div class="avatar" style="left:673px" role="img" aria-label="Client portrait"></div>
  <div class="stars" style="left:765px">★★★★★</div>
  <div class="t-name" style="left:765px">Owen Carrick</div>
  <svg class="abs" style="left:550px;top:2814px" width="100" height="18"><g fill="none" stroke="#1d86cf" stroke-width="1.6"><path d="M26 9H3M9 3L3 9l6 6"/><path d="M58 9h23M75 3l6 6-6 6"/></g></svg>
</section>

<!-- Global network -->
<section class="network"></section>
<h2 class="h2 abs" style="left:0;width:1200px;text-align:center;top:2962px">Our Global <span class="accent">Network</span></h2>
<div class="ph map" role="img" aria-label="Dotted world map marking distributor locations"></div>
<div class="map-tag">Fairview, IL 60100</div>

<!-- Contact -->
<section>
  <div class="ph contact-photo" role="img" aria-label="Laser cutting an ornate pattern in metal"></div>
  <h2 class="h2 abs" style="left:610px;top:3540px">Get In Touch With <span class="accent">Us</span></h2>
  <div class="underline" style="left:610px;top:3580px"></div>
  <div class="field" style="left:610px;top:3614px;width:216px">First name<svg width="14" height="14" viewBox="0 0 14 14"><circle cx="7" cy="4.5" r="3" fill="none" stroke="#d11f2d"/><path d="M2 13c0-3 2.5-5 5-5s5 2 5 5z" fill="none" stroke="#d11f2d"/></svg></div>
  <div class="field" style="left:842px;top:3614px;width:216px">Last name<svg width="14" height="14" viewBox="0 0 14 14"><circle cx="7" cy="4.5" r="3" fill="none" stroke="#d11f2d"/><path d="M2 13c0-3 2.5-5 5-5s5 2 5 5z" fill="none" stroke="#d11f2d"/></svg></div>
  <div class="field" style="left:610px;top:3671px;width:216px">Email<svg width="16" height="12" viewBox="0 0 16 12"><rect x="1" y="1" width="14" height="10" fill="none" stroke="#d11f2d"/><path d="M1 1l7 6 7-6" fill="none" stroke="#d11f2d"/></svg></div>
  <div class="field" style="left:842px;top:3671px;width:216px">Company<svg width="14" height="14" viewBox="0 0 14 14"><rect x="1" y="2" width="7" height="11" fill="none" stroke="#d11f2d"/><rect x="8" y="6" width="5" height="7" fill="none" stroke="#d11f2d"/></svg></div>
  <div class="field" style="left:610px;top:3727px;width:448px">Inquiry<svg width="12" height="8" viewBox="0 0 12 8"><path d="M1 1l5 5 5-5" fill="none" stroke="#333" stroke-width="1.5"/></svg></div>
  <div class="field tall" style="left:610px;top:3784px;width:448px;height:134px">Message<svg width="14" height="14" viewBox="0 0 14 14"><path d="M7 1.5c3.3 0 5.5 2.2 5.5 5S10.3 11.5 7 11.5c-.8 0-1.6-.1-2.3-.4L2 12.5l.8-2.3C2 9.3 1.5 8 1.5 6.5c0-2.8 2.2-5 5.5-5z" fill="none" stroke="#d11f2d"/></svg></div>
  <div class="btn" style="left:610px;top:3940px;width:109px;height:36px">Submit</div>
</section>

<!-- Footer -->
<footer class="footer"></footer>
<div class="f-brand"><span class="mark"></span>BROVIMARK</div>
<div class="f-call">CALL 555-014-2280</div>
<div class="f-col" style="left:538px"><h4>Quick Links</h4><a>Home</a><a>About Us</a><a>Products</a><a>Solutions</a><a>Industries</a><a>Services</a></div>
<div class="f-col" style="left:733px"><h4>Resources</h4><a>Privacy Policy</a><a>Terms Of Service</a><a>Contact</a></div>
<div class="f-col" style="left:920px"><h4>Contact Info</h4>
  <div class="f-contact"><svg width="14" height="16" viewBox="0 0 14 16"><path d="M7 15s5-5 5-9A5 5 0 0 0 2 6c0 4 5 9 5 9z" fill="#1d86cf"/><circle cx="7" cy="6" r="2" fill="#232325"/></svg>Fairview, IL 60100</div>
  <div class="f-contact"><svg width="16" height="12" viewBox="0 0 16 12"><rect width="16" height="12" rx="1" fill="#1d86cf"/><path d="M1 1l7 6 7-6" fill="none" stroke="#232325"/></svg>info@brovimark.com</div>
  <div class="f-contact"><svg width="15" height="15" viewBox="0 0 15 15"><path d="M3 1l3 3-2 2c1 2 3 4 5 5l2-2 3 3-2 2C7 14 1 8 1 3z" fill="#1d86cf"/></svg>555-014-2280</div>
</div>
<div class="f-rule"></div>
<div class="copy">Copyright © 2024 Brovimark Laser, LLC. All Rights Reserved.</div>
<div class="f-social" style="left:925px"></div>
<div class="f-social" style="left:961px"></div>
<div class="f-social" style="left:996px"></div>
<div class="f-social" style="left:1032px"></div>

</body>
</html>
```